Etiketten für Bio Seifen
Zielgruppe
Wir stellen hochwertig 'handgemachte' Bio-Seifen her. Die Zielgruppe ist von 3-99 Jahren und zusätzlich haben wir auch noch Seife für Hunde.
Der Firmenname ist 'Verdolina'
Aufgabenstellung
Das Etikett soll Bezug auf Natur, Bio, Nachhaltigkeit nehmen. Wir stellen uns 'weiche' Aquarellfarben vor...Seife: Lavendel, Calendular, 7 Kräuter etc.
Das Etikett soll auf eine Beutelschachtel. Die Schachtel hat eine Anmaße: Breite 55mm; Höhe 120mm; Tiefe 30mm
Das Etikett soll im vorderen- und hinteren Bereich zusammenhängend geklebt werden.
Das Etikett soll eine Abmaße von: Breite 51mm; Höhe 114mm haben (Vorderseite) Rückseite gleich.
Wir möchten die Produkte auch gerne nummerieren, d.h. jede Seife hat eine Nummer die nicht zu groß dargestellt werden soll aber trotzdem gut leserlich.
Wir haben noch ein paar Bilder hochgeladen wie wir uns das ungefähr vorstellen.

```html
<!DOCTYPE html>
<html lang="de">
<head>
<meta charset="utf-8">
<title>Verdolina – Seifenetiketten</title>
<link rel="stylesheet" href="https://fonts.googleapis.com/css2?family=Montserrat:wght@400;500&family=Libre+Baskerville&display=swap">
<style>
  :root {
    --navy: #0f3d72;
    --white: #ffffff;
    --lav-dark: #7a5fb0;
    --lav-mid: #b3a6dc;
    --lav-light: #eceaf7;
    --lav-tag: #eef0fb;
    --cal-dark: #eb9a3a;
    --cal-mid: #f4bf6a;
    --cal-light: #fbe2ae;
    --cal-tag: #ecd1a2;
    --herb-dark: #3cc6b3;
    --herb-mid: #7fdca8;
    --herb-light: #bdeccf;
    --herb-tag: #a8dcb6;
  }
  * { margin: 0; padding: 0; box-sizing: border-box; }
  html, body { width: 1200px; height: 838px; overflow: hidden; background: var(--white); }
  .sheet { position: relative; width: 1200px; height: 838px; }
  .label {
    position: absolute; top: 16px; width: 368px; height: 803px; overflow: hidden;
  }
  .label--lavendel { left: 24px; }
  .label--calendula { left: 420px; }
  .label--kraeuter { left: 816px; }
  .label__art { position: absolute; inset: 0; }
  .label--lavendel .label__art {
    background: radial-gradient(ellipse at 25% 55%, var(--lav-dark) 0%, var(--lav-mid) 45%, var(--lav-light) 85%);
  }
  .label--calendula .label__art {
    background: radial-gradient(ellipse at 40% 50%, var(--cal-dark) 0%, var(--cal-mid) 50%, var(--cal-light) 95%);
  }
  .label--kraeuter .label__art {
    background: linear-gradient(160deg, var(--herb-light) 0%, var(--herb-dark) 25%, var(--herb-mid) 60%, var(--herb-light) 100%);
  }
  .label__panel {
    position: absolute; left: 43px; top: 0; width: 280px; height: 404px;
    background: var(--white); text-align: center; color: var(--navy);
  }
  .brand {
    position: absolute; left: 0; right: 0; top: 165px;
    font-family: "Montserrat", sans-serif; font-weight: 500; font-size: 48px;
    letter-spacing: 1px; color: var(--navy);
  }
  .tagline {
    position: absolute; left: 0; right: 0; top: 240px;
    font-family: "Montserrat", sans-serif; font-weight: 400; font-size: 13.5px;
    letter-spacing: 1px; color: var(--navy);
  }
  .variant {
    position: absolute; left: 65px; top: 300px; width: 150px; height: 31px;
    border: 1.5px solid var(--navy); border-radius: 3px;
    font-family: "Libre Baskerville", serif; font-size: 15px; letter-spacing: 1px;
    line-height: 28px; color: var(--navy);
  }
  .label--lavendel .variant { background: var(--lav-tag); }
  .label--calendula .variant { background: var(--cal-tag); }
  .label--kraeuter .variant { background: var(--herb-tag); }
  .label__band {
    position: absolute; left: 43px; top: 404px; width: 280px; height: 21px;
    background: var(--navy); color: var(--white); text-align: center;
    font-family: "Montserrat", sans-serif; font-weight: 500; font-size: 13.5px; line-height: 21px;
  }
</style>
</head>
<body>
<main class="sheet">
  <section class="label label--lavendel">
    <div class="label__art" role="img" aria-label="Lila Aquarellhintergrund mit weißen Blüten-Linienzeichnungen"></div>
    <div class="label__panel">
      <div class="brand">Verdolina</div>
      <div class="tagline">NATUR AUF DER HAUT</div>
      <div class="variant">LAVENDEL</div>
    </div>
    <div class="label__band">Nachhaltige Bio-Seife</div>
  </section>

  <section class="label label--calendula">
    <div class="label__art" role="img" aria-label="Orange-gelber Aquarellhintergrund mit weißen Blüten-Linienzeichnungen"></div>
    <div class="label__panel">
      <div class="brand">Verdolina</div>
      <div class="tagline">NATUR AUF DER HAUT</div>
      <div class="variant">CALENDULAR</div>
    </div>
    <div class="label__band">Nachhaltige Bio-Seife</div>
  </section>

  <section class="label label--kraeuter">
    <div class="label__art" role="img" aria-label="Grün-türkiser Aquarellhintergrund mit weißen Blüten-Linienzeichnungen"></div>
    <div class="label__panel">
      <div class="brand">Verdolina</div>
      <div class="tagline">NATUR AUF DER HAUT</div>
      <div class="variant">7 KRÄUTER</div>
    </div>
    <div class="label__band">Nachhaltige Bio-Seife</div>
  </section>
</main>
</body>
</html>
```